Simple and Clean business card design

We would like the design to be simple clean and to incorporate our colors.

We are open to your design and talent, we have the dots in our logo as we think of it as data points and we connect data points for people.

We are open to see the great creative and clean design you bring to the table

Contact Information for Business Card

please include: name, position, email, phone and website

Font styles to use
Sans Serif

Requirements
Must have
• my colors incorporated, simplicity
Nice to have
• lots of white space, simplicity
Should not have
• complexicity/ complex art

```html
<!DOCTYPE html>
<html lang="en">
<head>
<meta charset="utf-8">
<title>Dotwise business card</title>
<link rel="stylesheet" href="https://fonts.googleapis.com/css2?family=Poppins:wght@400;500;700&display=swap">
<style>
  :root {
    --page-bg: #f4f4f4;
    --ink: #000000;
    --paper: #ffffff;
    --brand-blue: #4285f4;
    --muted-blue: #5580c0;
    --brand-red: #e94235;
    --brand-yellow: #f6bf16;
    --brand-green: #34a853;
  }
  * { box-sizing: border-box; margin: 0; padding: 0; }
  html, body {
    width: 1200px; height: 900px; overflow: hidden;
    background: var(--page-bg);
    font-family: "Poppins", sans-serif;
  }
  .sheet {
    width: 1200px; height: 900px;
    display: flex; flex-direction: column;
    align-items: center; justify-content: center; gap: 56px;
  }
  .card {
    width: 560px; height: 320px;
    border-radius: 18px;
    position: relative;
    overflow: hidden;
    box-shadow: 0 6px 18px rgba(0,0,0,0.18);
  }

  /* Front side */
  .card--front {
    background: var(--ink);
    display: flex; flex-direction: column;
    align-items: center; justify-content: center;
  }
  .brand-mark {
    display: flex; align-items: center; gap: 18px;
  }
  .brand-mark__dot {
    width: 58px; height: 58px; border-radius: 50%;
    background: var(--brand-blue);
  }
  .brand-mark__name {
    font-weight: 500; font-size: 104px; line-height: 1;
    letter-spacing: -2px;
    color: var(--paper);
  }
  .front-url {
    margin-top: 26px;
    font-size: 20px; font-weight: 400; letter-spacing: 1px;
  }
  .front-url .u-www { color: var(--brand-blue); }
  .front-url .u-name { color: var(--brand-red); }
  .front-url .u-dot { color: var(--brand-yellow); }
  .front-url .u-tld { color: var(--brand-green); }

  /* Back side */
  .card--back {
    background: var(--paper);
    padding: 44px 48px;
  }
  .card--back .brand-mark { gap: 12px; }
  .card--back .brand-mark__dot {
    width: 34px; height: 34px; background: var(--muted-blue);
  }
  .card--back .brand-mark__name {
    font-size: 62px; color: var(--ink); letter-spacing: -1px;
  }
  .holder { margin-top: 22px; }
  .holder__name {
    font-weight: 700; font-size: 22px; line-height: 1.1; color: var(--ink);
  }
  .holder__role {
    font-size: 18px; color: var(--muted-blue); line-height: 1.3;
  }
  .contacts { list-style: none; margin-top: 12px; }
  .contacts__item {
    display: flex; align-items: center; gap: 10px;
    font-size: 15px; color: var(--ink); line-height: 1.65;
  }
  .contacts__icon { width: 16px; height: 16px; flex: none; }
</style>
</head>
<body>
<main class="sheet">

  <section class="card card--front" aria-label="Card front">
    <div class="brand-mark">
      <span class="brand-mark__dot"></span>
      <span class="brand-mark__name">Dotwise</span>
    </div>
    <p class="front-url"><span class="u-www">www.</span><span class="u-name">Dotwise</span><span class="u-dot">.</span><span class="u-tld">io</span></p>
  </section>

  <section class="card card--back" aria-label="Card back">
    <div class="brand-mark">
      <span class="brand-mark__dot"></span>
      <span class="brand-mark__name">Dotwise</span>
    </div>
    <div class="holder">
      <p class="holder__name">Dotwise.io</p>
      <p class="holder__role">Founder/ CEO</p>
    </div>
    <ul class="contacts">
      <li class="contacts__item">
        <svg class="contacts__icon" viewBox="0 0 16 16" aria-hidden="true"><path fill="var(--brand-green)" d="M3.6 1.5l2.3 2.4-1.3 1.8c.8 1.8 2.2 3.2 4 4l1.8-1.3 2.4 2.3-1.4 2.3C6.9 12.8 3.2 9.1 1.3 3z"/></svg>
        <span>555-204-1187</span>
      </li>
      <li class="contacts__item">
        <svg class="contacts__icon" viewBox="0 0 16 16" aria-hidden="true"><rect x="1" y="3.5" width="14" height="9.5" rx="1" fill="var(--brand-yellow)"/><path d="M1.5 4.2L8 9l6.5-4.8" fill="none" stroke="#fff" stroke-width="1.2"/></svg>
        <span>mara.quill@dotwise.io</span>
      </li>
      <li class="contacts__item">
        <svg class="contacts__icon" viewBox="0 0 16 16" aria-hidden="true"><circle cx="8" cy="8" r="7" fill="var(--brand-red)"/><path d="M1 8h14M8 1c-3 3.5-3 10.5 0 14M8 1c3 3.5 3 10.5 0 14" fill="none" stroke="#fff" stroke-width="1"/></svg>
        <span>www.Dotwise.io</span>
      </li>
    </ul>
  </section>

</main>
</body>
</html>
```